Brightbay Orthodontics business card design

Need a business card design that reflects our re-branding (orthodontic office - braces) and a new partnership with a pediatric dental office. We would like to include "for adults and children" on the card as well so adults know they are welcome to get their braces here as well. Office design is modern and would like business card to reflect a modern type look. Here's the text we would like to be included on the card:

Darren Wolcott, DDS, MSD
5214 West Linden Avenue, Suite 204
Harlow Springs, CO 76991
555-418-2637
www.brightbayortho.example
info@brightbayortho.example

Can we add the following to the existing designs? Darren Wolcott, DDS, MSD 5214 West Linden Avenue, Suite 204 Harlow Springs, CO 76991 555-418-2637

Does anyone have any more vertical designs available? Thanks!

Dental

```html
<!DOCTYPE html>
<html lang="en">
<head>
<meta charset="utf-8">
<title>Brightbay Orthodontics – Business Card</title>
<link rel="stylesheet" href="https://fonts.googleapis.com/css2?family=Questrial&family=Didact+Gothic&display=swap">
<style>
  :root {
    --page-bg: #e9e7e4;
    --card-bg: #ffffff;
    --ink: #333333;
    --ink-soft: #5a5a5a;
    --brand-ink: #3b3b3b;
    --accent-blue: #1e88d0;
    --band: #f1f1f1;
  }
  * { box-sizing: border-box; margin: 0; padding: 0; }
  html, body {
    width: 1200px; height: 913px; overflow: hidden;
    background: var(--page-bg);
  }
  .stage {
    width: 1200px; height: 913px;
    display: flex; align-items: center; justify-content: center;
  }
  .card {
    position: relative;
    width: 380px; height: 666px;
    background: var(--card-bg);
    box-shadow: 0 6px 24px rgba(0,0,0,0.12);
    font-family: "Questrial", "Century Gothic", sans-serif;
    color: var(--ink);
  }
  .doctor {
    position: absolute; top: 38px; right: 34px;
    text-align: right;
    font-family: "Didact Gothic", "Century Gothic", sans-serif;
    color: var(--ink-soft);
  }
  .doctor-name { font-size: 27px; letter-spacing: 0.5px; }
  .doctor-title { font-size: 14px; margin-top: 2px; letter-spacing: 0.5px; }

  .brand {
    position: absolute; top: 122px; left: 34px; right: 30px;
    display: flex; align-items: center; gap: 14px;
  }
  .brand-dot {
    flex: none; width: 46px; height: 46px; border-radius: 50%;
    background: var(--accent-blue);
  }
  .brand-name {
    font-size: 33px; line-height: 1.05; color: var(--brand-ink);
  }
  .tagline {
    position: absolute; top: 206px; left: 34px;
    font-size: 14px; letter-spacing: 2.6px; text-transform: uppercase;
    color: var(--ink);
  }

  .contacts {
    position: absolute; top: 290px; left: 0; right: 0;
    list-style: none;
  }
  .contact {
    display: flex; align-items: center; gap: 12px;
    background: var(--band);
    padding: 0 14px 0 34px;
    height: 42px; margin-bottom: 8px;
    font-size: 14.5px;
  }
  .contact--phone { width: 70%; }
  .contact--web { width: 84%; }
  .contact--mail { width: 90%; }
  .contact--address {
    width: 96%; height: 74px; align-items: flex-start; padding-top: 12px;
    line-height: 1.7;
  }
  .contact-icon { flex: none; width: 20px; height: 20px; fill: var(--accent-blue); }
</style>
</head>
<body>
<main class="stage">
  <article class="card">
    <header class="doctor">
      <p class="doctor-name">Darren Wolcott</p>
      <p class="doctor-title">DDS, MSD</p>
    </header>

    <div class="brand">
      <span class="brand-dot" aria-hidden="true"></span>
      <p class="brand-name">Brightbay<br>Orthodontics</p>
    </div>
    <p class="tagline">For Adults &amp; Children</p>

    <ul class="contacts">
      <li class="contact contact--phone">
        <svg class="contact-icon" viewBox="0 0 20 20" aria-hidden="true">
          <rect x="0" y="0" width="20" height="20" rx="3"/>
          <path d="M5 6c0 5 4 9 9 9l1.5-2-2.5-1.5-1.2 1.1c-1.6-.8-2.9-2.1-3.7-3.7L9.2 7.7 7.7 5.2z" fill="#fff"/>
        </svg>
        <span>555-418-2637</span>
      </li>
      <li class="contact contact--web">
        <svg class="contact-icon" viewBox="0 0 20 20" aria-hidden="true">
          <circle cx="10" cy="10" r="10"/>
          <circle cx="10" cy="10" r="6" fill="none" stroke="#fff" stroke-width="1.4"/>
          <path d="M4 10h12M10 4c-2.5 3-2.5 9 0 12M10 4c2.5 3 2.5 9 0 12" fill="none" stroke="#fff" stroke-width="1.2"/>
        </svg>
        <span>www.brightbayortho.example</span>
      </li>
      <li class="contact contact--mail">
        <svg class="contact-icon" viewBox="0 0 20 20" aria-hidden="true">
          <rect x="0" y="3" width="20" height="14" rx="1.5"/>
          <path d="M1 4.5l9 7 9-7" fill="none" stroke="#fff" stroke-width="1.4"/>
        </svg>
        <span>info@brightbayortho.example</span>
      </li>
      <li class="contact contact--address">
        <svg class="contact-icon" viewBox="0 0 20 20" aria-hidden="true">
          <path d="M10 0a7 7 0 0 0-7 7c0 5 7 13 7 13s7-8 7-13a7 7 0 0 0-7-7z"/>
          <circle cx="10" cy="7" r="2.6" fill="#fff"/>
        </svg>
        <span>5214 West Linden Avenue, Suite 204<br>Harlow Springs, CO 76991</span>
      </li>
    </ul>
  </article>
</main>
</body>
</html>
```